professional business card design for technology company

We are a small technology consulting firm, specialising in consulting based around Cloud and Managed services. Our colour scheme is yellow, blue and white, as you can see in the logos. Although we are based in melbourne australia, due to the nature of our work, our clients can be located anywhere. We are looking for a clean, professional, positive look - similar to our company logo

Target Market(s)

small business

Industry/Entity Type

Business

Contact Information for Business Card

eye catching, designed to incorporate some level of raised printing. Must contain website address, phone number, name and job title

Requirements
Must have
• Logo (attached) - use of the same colour scheme

```html
<!DOCTYPE html>
<html lang="en">
<head>
<meta charset="utf-8">
<title>Skyvane business card</title>
<link href="https://fonts.googleapis.com/css2?family=Lato:wght@400;700;900&display=swap" rel="stylesheet">
<style>
  :root {
    --backdrop: #1c1c1c;
    --card-dark: #4a4a4b;
    --card-light: #f4f4f4;
    --brand-blue: #2f93d6;
    --brand-yellow: #e8c51a;
    --ink: #1e1e1e;
    --ink-soft: #4a4a4a;
    --strip-grey: #5a5a5a;
    --white: #ffffff;
  }
  * { box-sizing: border-box; margin: 0; padding: 0; }
  html, body {
    width: 1200px; height: 873px; overflow: hidden;
    background: var(--backdrop);
    font-family: "Lato", sans-serif;
  }
  .canvas { position: relative; width: 1200px; height: 873px; }

  .card {
    position: absolute; width: 540px; height: 309px;
    overflow: hidden; box-shadow: 0 14px 30px rgba(0,0,0,.55);
  }

  /* Front */
  .card--front { left: 40px; top: 282px; background: var(--card-dark); }
  .front__brand {
    position: absolute; left: 60px; top: 110px;
    display: flex; align-items: center; gap: 14px;
  }
  .brand__dot {
    width: 30px; height: 30px; border-radius: 50%;
    background: var(--brand-blue);
  }
  .front__name {
    font-weight: 900; font-size: 52px; color: var(--white); letter-spacing: -1px;
  }
  .front__divider {
    position: absolute; left: 340px; top: 200px; width: 2px; height: 50px;
    background: linear-gradient(to bottom, transparent, #bdbdbd, transparent);
  }
  .front__tagline {
    position: absolute; left: 360px; top: 216px;
    font-weight: 700; font-size: 13px; color: var(--brand-yellow);
  }
  .front__web {
    position: absolute; left: 60px; top: 262px;
    font-weight: 700; font-size: 15px; color: var(--brand-blue);
  }

  /* Back */
  .card--back { left: 620px; top: 282px; background: var(--card-light); }
  .back__brand {
    position: absolute; left: 42px; top: 90px;
    display: flex; align-items: center; gap: 12px;
  }
  .back__brand .brand__dot { width: 26px; height: 26px; }
  .back__name {
    font-weight: 900; font-size: 40px; color: var(--ink-soft); letter-spacing: -1px;
  }
  .back__web {
    position: absolute; left: 0; width: 290px; top: 176px; text-align: center;
    font-weight: 700; font-size: 14px; color: var(--ink-soft);
  }
  .back__web span { color: var(--brand-blue); }
  .back__address {
    position: absolute; left: 0; width: 290px; top: 208px; text-align: center;
    font-weight: 700; font-size: 15px; line-height: 1.3; color: var(--brand-blue);
  }
  .back__divider {
    position: absolute; left: 290px; top: 18px; width: 2px; height: 200px;
    background: linear-gradient(to bottom, transparent, var(--brand-blue) 30%, var(--brand-blue) 60%, transparent);
  }
  .person { position: absolute; left: 314px; top: 34px; }
  .person__name { font-weight: 900; font-size: 18px; color: var(--brand-blue); }
  .person__role { font-weight: 700; font-size: 12px; color: var(--ink); margin-top: 2px; }

  .contacts {
    position: absolute; left: 314px; top: 142px; list-style: none;
  }
  .contacts li {
    display: flex; align-items: center; gap: 8px;
    font-weight: 700; font-size: 14px; color: var(--ink); height: 22px;
  }
  .contacts svg { width: 18px; height: 18px; flex: none; }

  .back__band { position: absolute; left: 0; bottom: 0; width: 540px; height: 40px; }
</style>
</head>
<body>
<main class="canvas">

  <section class="card card--front" aria-label="Card front">
    <div class="front__brand">
      <span class="brand__dot"></span>
      <span class="front__name">Skyvane</span>
    </div>
    <div class="front__divider"></div>
    <p class="front__tagline">Your Slogan / Tagline Here</p>
    <p class="front__web">www.skyvane.com</p>
  </section>

  <section class="card card--back" aria-label="Card back">
    <div class="back__brand">
      <span class="brand__dot"></span>
      <span class="back__name">Skyvane</span>
    </div>
    <p class="back__web">www.<span>skyvane</span>.com</p>
    <p class="back__address">2200 Harbor Lane #210<br>Palm Grove, Florida 33400</p>

    <div class="back__divider"></div>

    <div class="person">
      <p class="person__name">Daniel R. Hollis</p>
      <p class="person__role">Broker / Owner</p>
    </div>

    <ul class="contacts">
      <li>
        <svg viewBox="0 0 20 20" aria-hidden="true"><circle cx="10" cy="10" r="10" fill="var(--brand-blue)"/><path d="M6 5.5h2.2l1 2.4-1.3 1a6 6 0 0 0 3.2 3.2l1-1.3 2.4 1V14a1 1 0 0 1-1 1A9 9 0 0 1 5 6.5a1 1 0 0 1 1-1z" fill="var(--white)"/></svg>
        555-210-4481
      </li>
      <li>
        <svg viewBox="0 0 20 20" aria-hidden="true"><circle cx="10" cy="10" r="10" fill="var(--brand-blue)"/><rect x="7" y="4.5" width="6" height="11" rx="1" fill="var(--white)"/><rect x="8" y="6" width="4" height="7" fill="var(--brand-blue)"/></svg>
        555-210-4482
      </li>
      <li>
        <svg viewBox="0 0 20 20" aria-hidden="true"><circle cx="10" cy="10" r="10" fill="var(--brand-blue)"/><rect x="7.5" y="4.5" width="5" height="4" fill="var(--white)"/><rect x="5" y="8.5" width="10" height="5" rx="1" fill="var(--white)"/><rect x="7.5" y="12" width="5" height="3.5" fill="var(--white)"/></svg>
        555-210-4483
      </li>
      <li>
        <svg viewBox="0 0 20 20" aria-hidden="true"><circle cx="10" cy="10" r="10" fill="var(--brand-blue)"/><rect x="5" y="6.5" width="10" height="7" fill="var(--white)"/><path d="M5 6.5l5 4 5-4" fill="none" stroke="var(--brand-blue)" stroke-width="1.2"/></svg>
        dan.hollis@mailbox.com
      </li>
    </ul>

    <svg class="back__band" viewBox="0 0 540 40" preserveAspectRatio="none" aria-hidden="true">
      <path d="M0 20 H310 Q322 20 326 8 Q330 0 342 0 H540 V40 H0 Z" fill="var(--brand-blue)"/>
      <path d="M0 24 H318 Q324 24 326 18 V40 H0 Z" fill="var(--strip-grey)"/>
    </svg>
  </section>

</main>
</body>
</html>
```